Calloway needs a modernized design

We would like a modern update (that can be responsive) to our existing website. Attached are the two existing pages we would like new concepts of - our home page and a page about one of our locations.

Calloway is provides executive offices and virtual office services. Startups, law firms, and financial services are our primary clients. We would like a professional, clean design, leaning towards minimalist. We intend to greatly reduce/eliminate the long paragraphs of text.

Requirements
Must have
• A design that can be responsive
Nice to have
• Large image(s) on home page that rotate.

```html
<!DOCTYPE html>
<html lang="en">
<head>
<meta charset="utf-8">
<title>Calloway Business Centers</title>
<link href="https://fonts.googleapis.com/css2?family=Roboto:ital,wght@0,400;0,500;0,700;1,400&display=swap" rel="stylesheet">
<style>
:root{
  --navy:#0c0c7c;
  --navy-dark:#08085e;
  --footer:#0e0e82;
  --gray-band:#eeeeee;
  --text-gray:#8a8a8a;
  --line:#d6d6d6;
  --white:#ffffff;
}
*{margin:0;padding:0;box-sizing:border-box}
html,body{width:1200px;height:3041px;overflow:hidden}
body{font-family:"Roboto",Arial,sans-serif;background:var(--white);color:var(--navy);position:relative}
.section{position:absolute;left:0;width:1200px}

/* header */
.site-header{top:0;height:116px}
.brand{position:absolute;left:77px;top:14px;display:flex;align-items:center;gap:14px}
.brand-mark{width:90px;height:90px;border-radius:50%;background:var(--navy)}
.brand-name{font-size:44px;font-weight:700;color:var(--navy);letter-spacing:1px}
.header-phones{position:absolute;right:80px;top:34px;display:flex;align-items:center;font-size:19px;color:#555}
.header-phones .city{margin-right:14px}
.phone-ring{width:48px;height:48px;border:2px solid var(--navy);border-radius:50%;display:flex;align-items:center;justify-content:center;margin-right:10px}
.header-phones .sep{width:1px;height:44px;background:var(--line);margin:0 14px}

/* nav */
.main-nav{top:116px;height:60px;background:var(--navy);display:flex;padding-left:77px}
.main-nav a{color:var(--white);text-decoration:none;font-size:17px;display:flex;align-items:center;padding:0 24px}
.main-nav a.active{background:var(--navy-dark)}

/* hero */
.hero{top:176px;height:502px}
.hero-image{position:absolute;inset:0;background:linear-gradient(100deg,#dfe6ee 0%,#b9c4d1 30%,#33374a 55%,#d8dde4 75%,#f2f4f7 100%)}
.hero-arrow{position:absolute;top:246px;width:52px;height:52px;border:2px solid #555;border-radius:50%;background:rgba(255,255,255,.6);display:flex;align-items:center;justify-content:center}
.hero-arrow.prev{left:12px}.hero-arrow.next{right:14px}
.hero-dots{position:absolute;left:690px;top:462px;display:flex;gap:10px}
.hero-dots span{width:11px;height:11px;border-radius:50%;background:rgba(255,255,255,.55)}
.quote-form{position:absolute;left:746px;top:64px;width:376px;height:386px;background:var(--navy);padding:24px 22px}
.quote-form h2{color:var(--white);font-weight:400;font-size:31px;text-align:center;margin-bottom:16px}
.quote-form .field{height:46px;background:var(--white);margin-bottom:7px;font-size:13px;color:#aaa;padding:14px 16px}
.quote-form .submit{display:block;margin:14px auto 0;width:132px;height:50px;background:var(--white);color:var(--navy);font-size:20px;text-align:center;line-height:50px}

/* features */
.features{top:678px;height:292px;background:var(--gray-band);display:flex;padding:54px 78px 0}
.feature{flex:1;text-align:center;border-right:1px solid var(--line);height:180px}
.feature:last-child{border-right:none}
.feature-icon{width:106px;height:106px;border:2px solid var(--navy);border-radius:50%;margin:0 auto 22px;display:flex;align-items:center;justify-content:center}
.feature-icon.filled{background:var(--navy)}
.feature p{font-size:17px;line-height:26px;text-transform:uppercase}

/* welcome */
.welcome{top:970px;height:416px;text-align:center}
.section-title{font-size:41px;font-weight:400;color:var(--navy)}
.welcome .section-title{margin-top:62px}
.body-copy{font-size:14.5px;line-height:26px;color:var(--text-gray);width:790px;margin:18px auto 0}
.btn{display:inline-block;background:var(--navy);color:var(--white);font-size:19px;padding:0 26px;height:60px;line-height:60px;margin-top:16px}

/* services */
.services{top:1386px;height:479px;text-align:center}
.services-bg{position:absolute;inset:0;background:radial-gradient(ellipse at 50% 60%,#3a3a3a 0%,#1c1c1c 60%,#0d0d0d 100%)}
.services .section-title{position:relative;color:var(--white);margin-top:58px}
.video-frame{position:absolute;left:335px;top:130px;width:558px;height:290px;background:#e7e7e9;border:4px solid #111}
.video-brand{position:absolute;left:52px;top:42px;display:flex;align-items:center;gap:22px}
.video-brand .mark{width:150px;height:150px;border-radius:50%;background:var(--navy)}
.video-brand .name{font-size:50px;font-weight:700;color:#243a6e;text-align:left}
.video-brand .tag{font-size:15px;color:#243a6e;letter-spacing:1px;margin-top:20px;font-weight:700}
.video-controls{position:absolute;left:0;bottom:0;width:100%;height:26px;background:#111;display:flex;align-items:center;padding:0 10px;gap:10px}
.video-controls .track{flex:1;height:3px;background:#888}

/* value */
.value{top:1865px;height:301px;background:var(--gray-band);text-align:center}
.value .section-title{margin-top:62px}
.value .body-copy{width:880px;font-size:14.5px}
.chevron{margin-top:10px}

/* testimonials */
.testimonials{top:2166px;height:431px;text-align:center}
.testimonials .section-title{margin-top:58px}
.quote-badge{width:76px;height:76px;border:2px solid var(--navy);border-radius:50%;margin:20px auto 0;display:flex;align-items:center;justify-content:center}
.testimonial-text{font-style:italic;font-size:14.5px;line-height:26px;color:#777;width:820px;margin:18px auto 0}
.testimonial-name{font-size:16px;margin-top:6px;color:var(--navy)}
.testimonial-site{font-size:14.5px;color:#777;margin-top:4px}

/* partners */
.partners{top:2597px;height:131px;background:var(--gray-band);display:flex;align-items:center;justify-content:space-between;padding:0 100px}
.partner{width:130px;height:40px;background:#c4c4c4;border-radius:4px}

/* footer */
.site-footer{top:2728px;height:313px;background:var(--footer);color:var(--white)}
.footer-badge{position:absolute;left:104px;top:42px;width:180px;height:180px;border-radius:50%;background:#8e95a6;border:6px solid #cfd3dc}
.footer-col{position:absolute;top:40px}
.footer-col h3{font-size:20px;font-weight:400;letter-spacing:.5px;margin-bottom:18px}
.links{display:grid;grid-template-columns:128px 110px;row-gap:12px;font-size:14px;padding-left:0;list-style:none}
.links li{display:flex;align-items:center;gap:14px}
.links li::before{content:"";width:9px;height:9px;border-radius:50%;background:var(--white)}
.contact-row{display:flex;align-items:center;gap:22px;margin-bottom:22px;font-size:15px;line-height:24px}
.contact-row .ring{width:46px;height:46px;border:2px solid var(--white);border-radius:50%;display:flex;align-items:center;justify-content:center}
.touch-row{display:flex;gap:16px;font-size:14px;line-height:23px;margin-bottom:16px}
.footer-bottom{position:absolute;left:77px;right:77px;top:252px;display:flex;justify-content:space-between;align-items:center;font-size:14px}
.footer-bottom strong{font-weight:500}
.social{display:flex;gap:12px}
.social span{width:40px;height:40px;border-radius:50%;border:2px solid var(--white);background:var(--white);opacity:.95}
</style>
</head>
<body>

<header class="section site-header">
  <div class="brand"><div class="brand-mark"></div><span class="brand-name">CALLOWAY</span></div>
  <div class="header-phones">
    <span class="city">Dallas</span>
    <span class="phone-ring"><svg width="22" height="22" viewBox="0 0 24 24"><path d="M6.6 10.8a15 15 0 006.6 6.6l2.2-2.2a1 1 0 011-.25 11 11 0 003.5.56 1 1 0 011 1V20a1 1 0 01-1 1A17 17 0 013 4a1 1 0 011-1h3.5a1 1 0 011 1 11 11 0 00.56 3.5 1 1 0 01-.25 1z" fill="none" stroke="#0c0c7c" stroke-width="1.8"/></svg></span>
    <span>214.555.0142</span>
    <span class="sep"></span>
    <span class="city">Houston</span>
    <span class="phone-ring"><svg width="22" height="22" viewBox="0 0 24 24"><path d="M6.6 10.8a15 15 0 006.6 6.6l2.2-2.2a1 1 0 011-.25 11 11 0 003.5.56 1 1 0 011 1V20a1 1 0 01-1 1A17 17 0 013 4a1 1 0 011-1h3.5a1 1 0 011 1 11 11 0 00.56 3.5 1 1 0 01-.25 1z" fill="none" stroke="#0c0c7c" stroke-width="1.8"/></svg></span>
    <span>713.555.0187</span>
  </div>
</header>

<nav class="section main-nav">
  <a class="active">HOME</a><a>PROPERTIES</a><a>VIRTUAL TOURS</a><a>PHOTOS</a><a>BROKER REFERRALS</a>
</nav>

<section class="section hero">
  <div class="hero-image" role="img" aria-label="Two smiling businesswomen shaking hands in front of a modern glass office building"></div>
  <span class="hero-arrow prev"><svg width="18" height="18" viewBox="0 0 18 18"><path d="M12 2L5 9l7 7" fill="none" stroke="#444" stroke-width="2"/></svg></span>
  <span class="hero-arrow next"><svg width="18" height="18" viewBox="0 0 18 18"><path d="M6 2l7 7-7 7" fill="none" stroke="#444" stroke-width="2"/></svg></span>
  <div class="hero-dots"><span></span><span></span><span></span></div>
  <form class="quote-form">
    <h2>GET A QUOTE</h2>
    <div class="field">Name *</div>
    <div class="field">Email *</div>
    <div class="field">Company *</div>
    <div class="field">Phone *</div>
    <span class="submit">SUBMIT</span>
  </form>
</section>

<section class="section features">
  <div class="feature">
    <div class="feature-icon filled"><svg width="54" height="54" viewBox="0 0 54 54" fill="none" stroke="#fff" stroke-width="2.5"><rect x="8" y="8" width="22" height="16"/><path d="M4 30h46M10 30v18M44 30v18M32 30v14h12"/><rect x="34" y="14" width="8" height="16"/></svg></div>
    <p>Executive Office<br>Suites</p>
  </div>
  <div class="feature">
    <div class="feature-icon"><svg width="56" height="56" viewBox="0 0 56 56" fill="#0c0c7c"><ellipse cx="28" cy="30" rx="16" ry="8"/><circle cx="12" cy="18" r="4"/><circle cx="28" cy="13" r="4"/><circle cx="44" cy="18" r="4"/><circle cx="10" cy="42" r="4"/><circle cx="46" cy="42" r="4"/></svg></div>
    <p>On- Demand Meeting<br>Rooms</p>
  </div>
  <div class="feature">
    <div class="feature-icon"><svg width="56" height="56" viewBox="0 0 56 56" fill="none" stroke="#0c0c7c" stroke-width="2.5"><rect x="6" y="10" width="28" height="20"/><path d="M11 26v-6M17 26v-10M23 26v-4M29 26v-12M20 30v16M14 46h12"/><circle cx="44" cy="16" r="4" fill="#0c0c7c"/><path d="M40 24h8v22" fill="#0c0c7c"/></svg></div>
    <p>On - Demand Trainning<br>Rooms</p>
  </div>
  <div class="feature">
    <div class="feature-icon"><svg width="56" height="56" viewBox="0 0 56 56" fill="none" stroke="#0c0c7c" stroke-width="2.5"><circle cx="18" cy="12" r="4" fill="#0c0c7c"/><path d="M18 18v14h10M18 32l-4 14M28 32v14"/><rect x="30" y="12" width="18" height="14"/><path d="M26 30h24M44 30v16"/></svg></div>
    <p>Virtual Offices<br>Solutions</p>
  </div>
  <div class="feature">
    <div class="feature-icon"><svg width="56" height="56" viewBox="0 0 56 56" fill="none" stroke="#0c0c7c" stroke-width="2.5"><rect x="8" y="8" width="40" height="28" rx="2"/><circle cx="22" cy="20" r="4" fill="#0c0c7c"/><path d="M16 32c0-5 12-5 12 0" fill="#0c0c7c"/><path d="M28 36v6M18 44h20"/><circle cx="42" cy="44" r="5" fill="#0c0c7c"/></svg></div>
    <p>Video Conference<br>Solutions</p>
  </div>
</section>

<section class="section welcome">
  <h2 class="section-title">WELCOME TO CALLOWAY</h2>
  <p class="body-copy">Either you need Dallas/Ft. Worth Office Space, Dallas Executive Suites, Ft. Worth Executive Suites, Houston Office Space, Houston Executive Suites, or maybe you simply need a place to stop in and use an on-demand office or meeting room from time to time or utilize our local business phone numbers, phone answering or business addresses through one of our virtual office solutions. At Calloway, you will always find affordable and beautiful, professional properties. To make decisions easy for our full service executive suite clients.e, phone answering and 55 hours of conference room time per month (alone a value of over $1,600/mo).</p>
  <span class="btn">KNOW MORE</span>
</section>

<section class="section services">
  <div class="services-bg" role="img" aria-label="Dim boardroom with a long conference table and leather chairs"></div>
  <h2 class="section-title">OUR SERVICES</h2>
  <div class="video-frame">
    <div class="video-brand">
      <div class="mark"></div>
      <div><div class="name">CALLOWAY</div><div class="tag">VIRTUAL OFFICE SERVICES</div></div>
    </div>
    <div class="video-controls">
      <svg width="12" height="12" viewBox="0 0 12 12" fill="#ddd"><rect x="2" y="1" width="3" height="10"/><rect x="7" y="1" width="3" height="10"/></svg>
      <span class="track"></span>
      <svg width="14" height="12" viewBox="0 0 14 12" fill="#ddd"><path d="M1 4h3l4-3v10L4 8H1z"/></svg>
      <svg width="12" height="12" viewBox="0 0 12 12" fill="none" stroke="#ddd" stroke-width="2"><rect x="1" y="1" width="10" height="10"/></svg>
    </div>
  </div>
</section>

<section class="section value">
  <h2 class="section-title">OUR VALUE</h2>
  <p class="body-copy">Either you need Dallas/Ft. Worth Office Space, Dallas Executive Suites, Ft. Worth Executive Suites, Houston Office Space, Houston Executive Suites, or maybe you simply need a place to stop in and use an on-demand office or meeting room from time to time or utilize our local business phone numbers, phone answering.</p>
  <svg class="chevron" width="20" height="20" viewBox="0 0 20 20" fill="none" stroke="#0c0c7c" stroke-width="2.4"><path d="M4 3l6 6 6-6M4 10l6 6 6-6"/></svg>
</section>

<section class="section testimonials">
  <h2 class="section-title">TESTIMONIALS</h2>
  <div class="quote-badge"><svg width="32" height="26" viewBox="0 0 32 26" fill="#0c0c7c"><path d="M0 14C0 6 4 1 12 0v5c-4 1-6 4-6 7h6v14H0zM18 14c0-8 4-13 12-14v5c-4 1-6 4-6 7h6v14H18z"/></svg></div>
  <p class="testimonial-text">"Thanks to your helpful IT person, I now have a more professional website and email address, remote access to my PC, and a comprehensive backup, antivirus and anti-spyware solution. I even have all of my contacts and my calendar organized and loaded into my pda."</p>
  <p class="testimonial-name">- Dan Whitfield</p>
  <p class="testimonial-site">(example.com)</p>
</section>

<section class="section partners">
  <span class="partner"></span><span class="partner"></span><span class="partner"></span><span class="partner"></span><span class="partner"></span><span class="partner"></span>
</section>

<footer class="section site-footer">
  <div class="footer-badge"></div>
  <div class="footer-col" style="left:345px">
    <h3>USEFULL LINKS</h3>
    <ul class="links">
      <li>About us</li><li>Specials</li>
      <li>Contact us</li><li>Site Map</li>
      <li>Testimonials</li><li>Privacy</li>
      <li>FAQs</li><li></li>
      <li>Careers</li>
    </ul>
  </div>
  <div class="footer-col" style="left:609px">
    <h3>CONTACT US</h3>
    <div class="contact-row"><span class="ring"><svg width="20" height="20" viewBox="0 0 24 24"><path d="M6.6 10.8a15 15 0 006.6 6.6l2.2-2.2a1 1 0 011-.25 11 11 0 003.5.56 1 1 0 011 1V20a1 1 0 01-1 1A17 17 0 013 4a1 1 0 011-1h3.5a1 1 0 011 1 11 11 0 00.56 3.5 1 1 0 01-.25 1z" fill="#fff"/></svg></span><div>Dallas<br>214.555.0142</div></div>
    <div class="contact-row"><span class="ring"><svg width="20" height="20" viewBox="0 0 24 24"><path d="M6.6 10.8a15 15 0 006.6 6.6l2.2-2.2a1 1 0 011-.25 11 11 0 003.5.56 1 1 0 011 1V20a1 1 0 01-1 1A17 17 0 013 4a1 1 0 011-1h3.5a1 1 0 011 1 11 11 0 00.56 3.5 1 1 0 01-.25 1z" fill="#fff"/></svg></span><div>Houston<br>713.555.0187</div></div>
  </div>
  <div class="footer-col" style="left:874px">
    <h3>GET IN TOUCH</h3>
    <div class="touch-row"><svg width="18" height="24" viewBox="0 0 18 24" fill="none" stroke="#fff" stroke-width="1.6"><path d="M9 23S2 14 2 9a7 7 0 0114 0c0 5-7 14-7 14z"/><circle cx="9" cy="9" r="2.5"/></svg><div>Calloway Business Centers 4120<br>Elm Crest Parkway Suite<br>300 Dallas, Texas 75204</div></div>
    <div class="touch-row"><svg width="18" height="18" viewBox="0 0 24 24"><path d="M6.6 10.8a15 15 0 006.6 6.6l2.2-2.2a1 1 0 011-.25 11 11 0 003.5.56 1 1 0 011 1V20a1 1 0 01-1 1A17 17 0 013 4a1 1 0 011-1h3.5a1 1 0 011 1 11 11 0 00.56 3.5 1 1 0 01-.25 1z" fill="none" stroke="#fff" stroke-width="1.8"/></svg><div>713.555.0187</div></div>
    <div class="touch-row"><svg width="18" height="14" viewBox="0 0 18 14" fill="none" stroke="#fff" stroke-width="1.6"><rect x="1" y="1" width="16" height="12"/><path d="M1 1l8 7 8-7"/></svg><div>Offices@CallowayOffices.com</div></div>
  </div>
  <div class="footer-bottom">
    <span>© 2016 <strong>CALLOWAY BUSINESS CENTERS</strong> All rights reserved.</span>
    <div class="social"><span></span><span></span><span></span><span></span><span></span></div>
  </div>
</footer>

</body>
</html>
```